Dietary Supplement Label Design - Reusable

Design client specific, company specific, dietary supplement labels for 4 product lines (4 labels).
-Must meet FDA regulation on dietary supplement labels.
-Must be ready to print by manufacturer.
-Must include barcode per product line (4 barcodes)
-Labels must be attractive to the uploaded customer persona

Here is a summary of what I am uploading:
-Company brand information: Has description of a typical customer, and our logo picture. The design should be attractive to this customer type. Company name is Brookvale Wellness (https://www.brookvalewellness.example/). I'd expect a small logo picture to appear together with our web address, likely on the side or bottom of the label.
-General labels I like: Pictures of labels I like, and fonts I like. Just to give you a sense of what I have in mind to achieve in terms of label for the supplements. The label type you create should have elements, color matching/synergy from these label pictures.
-Label templates: There are 4 templates. The names of the supplements that we will use are in parentheses in the filenames of the label templates. They are: CalmHaven Max ; VitalSpark B-Complex ; SugarBalance Prime ; GutComfort

```html
<!DOCTYPE html>
<html lang="en">
<head>
<meta charset="utf-8">
<title>Brookvale Wellness Supplement Labels</title>
<link href="https://fonts.googleapis.com/css2?family=Montserrat:wght@400;600;700&family=Roboto+Condensed:wght@400;700&family=Tenor+Sans&display=swap" rel="stylesheet">
<style>
:root{
  --sheet:#e3e3e3;
  --white:#ffffff;
  --ink:#111111;
  --dark-text:#1a1a1a;
  --orange:#e4533a;
  --blue:#2a3ad0;
  --gold:#dfa20c;
  --plum:#2a1448;
  --band-red:#e5533a;
  --band-gold:#eaa91c;
  --band-blue:#2a56c6;
  --capsule:#5fb28a;
  --tick-yellow:#f3c53a;
  --tick-red:#e5533a;
  --tick-green:#7cc48f;
}
*{box-sizing:border-box;margin:0;padding:0}
html,body{width:852px;height:1200px;overflow:hidden;background:var(--sheet)}
body{position:relative;font-family:"Montserrat",sans-serif;color:var(--white)}
.label{position:absolute;left:62px;width:728px;height:257px;background:var(--bg);overflow:hidden}
.label--digest{top:64px;--bg:var(--orange);--tick:var(--tick-yellow);--strip:#cf4430}
.label--glycemic{top:336px;--bg:var(--blue);--tick:var(--tick-red);--strip:#2331b8}
.label--energy{top:608px;--bg:var(--gold);--tick:var(--tick-red);--strip:#cc920a}
.label--calm{top:880px;--bg:var(--plum);--tick:var(--tick-green);--strip:#21103c}

.usage{position:absolute;left:18px;top:18px;width:172px;font-size:6.6px;line-height:1.36;display:flex;flex-direction:column;gap:7px}
.usage b{font-weight:700}
.usage .keep{font-weight:700}
.label--energy .usage{color:var(--dark-text)}
.fda-note{border:0.7px solid rgba(255,255,255,.8);border-radius:4px;padding:4px 6px;font-weight:500}
.label--energy .fda-note{border:none;padding:0 6px}
.brand{display:flex;align-items:center;gap:6px;margin-top:2px}
.brand-mark{flex:none;width:40px;height:26px;background:#8fbf6a;border-radius:2px}
.brand-name{display:block;font-size:10.5px;font-weight:700;line-height:1;letter-spacing:-.3px;white-space:nowrap}
.brand-url{display:block;font-size:7px;font-weight:600;margin-top:1px;white-space:nowrap}

.front{position:absolute;left:232px;top:14px;width:270px}
.title{font-family:"Tenor Sans",sans-serif;font-weight:400;line-height:.86;letter-spacing:-1.5px;color:var(--white)}
.label--energy .title{color:var(--ink)}
.title sup{font-size:.32em;letter-spacing:0;vertical-align:top;position:relative;top:.3em}
.band{font-family:"Tenor Sans",sans-serif;display:block;width:198px;padding:3px 8px;font-size:12.5px;white-space:nowrap}
.band--red{background:var(--band-red)}
.band--gold{background:var(--band-gold)}
.band--blue{background:var(--band-blue)}
.benefits{list-style:none;font-family:"Tenor Sans",sans-serif;font-size:9.6px;line-height:1.2;margin-top:8px;display:flex;flex-direction:column;gap:5px}
.label--energy .benefits{color:#3a2a10}
.benefits li{display:flex;gap:4px}
.benefits svg{flex:none;width:8px;height:8px;margin-top:2px}
.badges{position:absolute;left:298px;bottom:14px;display:flex;gap:5px}
.badge{width:17px;height:17px;border-radius:50%;background:var(--white);border:2px solid #2f9a54}
.badge--mid{border-color:#23489b}

.art{position:absolute;border-radius:50%}
.capsules{position:absolute;left:397px;top:184px;width:58px;bottom:0;background:var(--capsule);border-radius:29px 29px 0 0;text-align:center;font-family:"Tenor Sans",sans-serif}
.capsules .count{font-size:34px;line-height:1;display:block;margin-top:6px;letter-spacing:-2px}
.capsules .word{font-size:10px;display:block;line-height:1}
.capsules .per{font-size:5px;display:block;border-top:.6px solid rgba(255,255,255,.6);margin-top:5px;padding-top:3px}

.facts{position:absolute;left:507px;top:20px;width:140px;background:var(--white);color:var(--ink);border:1px solid var(--ink);padding:3px 4px;font-family:"Roboto Condensed",sans-serif;overflow:hidden}
.facts h3{font-size:17px;font-weight:700;line-height:1;letter-spacing:-.3px;border-bottom:4px solid var(--ink);padding-bottom:3px;white-space:nowrap}
.facts .serving{font-size:6px;line-height:1.2;padding:2px 0;white-space:nowrap}
.facts table{width:100%;border-collapse:collapse;font-size:5.2px;line-height:1.25}
.facts th{font-weight:700;text-align:right;border-top:3px solid var(--ink);border-bottom:1px solid var(--ink);padding:1px 0;white-space:nowrap}
.facts td{border-bottom:.4px solid #777;padding:.3px 0;white-space:nowrap}
.facts td.num{text-align:right;padding-left:3px}
.facts td.blend{white-space:normal;font-size:4px;line-height:1.2;padding-left:5px}
.facts .note{font-size:5.4px;border-top:3px solid var(--ink);padding-top:1px;margin-top:1px;white-space:nowrap}
.facts--big table{font-size:5.6px}
.facts--dense table{font-size:4px;line-height:1.15}
.facts--dense h3{font-size:14px}
.other{position:absolute;left:505px;width:148px;font-size:5.2px;line-height:1.35}
.other b{font-weight:700}
.other .lot{display:block;margin-top:7px;font-size:4.6px}

.strip{position:absolute;left:656px;top:20px;width:44px;height:221px;border:.8px solid rgba(255,255,255,.8);background:var(--strip)}
.strip .code-zone{height:70px;border-bottom:.8px solid rgba(255,255,255,.8);background:var(--bg)}
.strip .distributor{position:absolute;left:6px;bottom:6px;width:146px;transform-origin:left bottom;transform:rotate(-90deg) translateY(100%);font-size:5.8px;line-height:1.35;white-space:nowrap}
.strip .distributor b{font-weight:700}
</style>
</head>
<body>

<section class="label label--digest">
  <div class="usage">
    <p><b>SUGGESTED USE:</b> As a dietary supplement, take one (1) capsule twice a day. For best results, take 20-30 min before a meal or as directed by your healthcare professional.</p>
    <p><b>CAUTION:</b> Do not exceed recommended dose. Pregnant or nursing mothers, children under the age of 18, and individuals with a known medical condition should consult a physician before using this or any dietary supplement.</p>
    <p class="keep">KEEP OUT OF REACH OF CHILDREN. DO NOT USE IF SAFETY SEAL IS DAMAGED OR MISSING. STORE IN A COOL, DRY PLACE.</p>
    <p class="fda-note">*These statements have not been evaluated by the Food and Drug Administration. This product is not intended to diagnose, treat, cure or prevent any disease.</p>
    <div class="brand"><span class="brand-mark"></span><span><span class="brand-name">BROOKVALE WELLNESS</span><span class="brand-url">www.brookvalewellness.example</span></span></div>
  </div>
  <div class="art" role="img" aria-label="Green leaf" style="left:200px;top:16px;width:46px;height:26px;background:linear-gradient(135deg,#4fae3c,#1f6b22)"></div>
  <div class="art" role="img" aria-label="Illustrated stomach with leaf" style="left:390px;top:104px;width:80px;height:78px;background:radial-gradient(circle,#e3604c,#a52a25)"></div>
  <div class="front">
    <h1 class="title" style="font-size:44px;margin:28px 0 10px 0">GutComfort<sup>TM</sup></h1>
    <span class="band band--blue">ENZYBLEND-PRO™</span>
    <span class="band band--gold">Dietary Supplement | 30-day supply</span>
    <ul class="benefits">
      <li><svg viewBox="0 0 10 10"><path d="M1 5l3 3 5-7" fill="none" stroke="var(--tick)" stroke-width="1.8"/></svg>Helps reduce bloating*</li>
      <li><svg viewBox="0 0 10 10"><path d="M1 5l3 3 5-7" fill="none" stroke="var(--tick)" stroke-width="1.8"/></svg>Improves nutrient absorption*</li>
      <li><svg viewBox="0 0 10 10"><path d="M1 5l3 3 5-7" fill="none" stroke="var(--tick)" stroke-width="1.8"/></svg>Helps ease heartburn*</li>
    </ul>
  </div>
  <div class="badges" style="left:297px"><span class="badge"></span><span class="badge badge--mid"></span><span class="badge"></span></div>
  <div class="capsules"><span class="count">60</span><span class="word">Capsules</span><span class="per">400mg per serving</span></div>
  <div class="facts facts--big" style="height:174px">
    <h3>Supplement Facts</h3>
    <p class="serving"><b>Serving Size:</b> 1 Veggie Capsule<br><b>Servings Per Container:</b> 60</p>
    <table>
      <tr><th></th><th>Amount Per Serving</th><th>%DV</th></tr>
      <tr><td>Enzyblend-Pro™<br>Enzyme Blend:<br>Fungal Protease from Aspergillus oryzae<br>Lactobacillus acidophilus<br>Lactobacillus casei<br>Lactobacillus plantarum</td><td class="num" style="vertical-align:top">2500 HUT/400mg</td><td class="num" style="vertical-align:top">**</td></tr>
      <tr><td>Bromelain</td><td class="num">90 GDU</td><td class="num">**</td></tr>
      <tr><td>Papain</td><td class="num">2670 TU</td><td class="num">**</td></tr>
      <tr><td>Fungal Lipase</td><td class="num">1500 FIP</td><td class="num">**</td></tr>
      <tr><td>Fungal Lactase</td><td class="num">600 LACU</td><td class="num">**</td></tr>
      <tr><td>Alpha Galactosidase</td><td class="num">300 GALU</td><td class="num">**</td></tr>
    </table>
    <p class="note">** Daily Value (DV) not established.</p>
  </div>
  <p class="other" style="top:208px"><b>Other Ingredients:</b> Hypromellose (vegetable capsule), Vegetable Magnesium Stearate, Silicon Dioxide<span class="lot">V3R0<br>Lot # and Expiration Date Printed on bottom of bottle</span></p>
  <div class="strip"><div class="code-zone"></div><p class="distributor"><b>Distributed By:</b> Brookvale Wellness LLC<br>1420 Alder Ridge Rd. Laramie, WY 82070<br>www.brookvalewellness.example 555-014-2290</p></div>
</section>

<section class="label label--glycemic">
  <div class="usage">
    <p><b>SUGGESTED USE:</b> As a dietary supplement, take one (1) veggie capsule once a day. If desired, take two capsules daily. For best results, take 20-30 min before a meal with an 8 fl oz. glass of water or as directed by your healthcare professional.</p>
    <p><b>CAUTION:</b> Do not exceed recommended dose. Pregnant or nursing mothers, children under the age of 18, and individuals with a known medical condition should consult a physician before using this or any dietary supplement.<br><span class="keep">KEEP OUT OF REACH OF CHILDREN. DO NOT USE IF SAFETY SEAL IS DAMAGED OR MISSING. STORE IN A COOL, DRY PLACE.</span></p>
    <p class="fda-note">*These statements have not been evaluated by the Food and Drug Administration. This product is not intended to diagnose, treat, cure or prevent any disease.</p>
    <div class="brand"><span class="brand-mark"></span><span><span class="brand-name">BROOKVALE WELLNESS</span><span class="brand-url">www.brookvalewellness.example</span></span></div>
  </div>
  <div class="art" role="img" aria-label="Glass molecule model" style="left:345px;top:52px;width:96px;height:70px;background:radial-gradient(circle,#d8ecef,#7fa7b4 70%,transparent 72%)"></div>
  <div class="front">
    <h1 class="title" style="font-size:36px;margin:4px 0 14px 0">SugarBalance<br>Prime<sup>TM</sup></h1>
    <span class="band band--red" style="font-size:11.5px">Supports Healthy Blood Sugar</span>
    <span class="band band--gold" style="padding:6px 8px">Dietary Supplement | 30-day supply</span>
    <ul class="benefits">
      <li><svg viewBox="0 0 10 10"><path d="M1 5l3 3 5-7" fill="none" stroke="var(--tick)" stroke-width="1.8"/></svg>Helps maintain stable blood<br>glucose levels*</li>
      <li><svg viewBox="0 0 10 10"><path d="M1 5l3 3 5-7" fill="none" stroke="var(--tick)" stroke-width="1.8"/></svg>Supports overall health<br>&amp; wellness*</li>
      <li><svg viewBox="0 0 10 10"><path d="M1 5l3 3 5-7" fill="none" stroke="var(--tick)" stroke-width="1.8"/></svg>Immune function support*</li>
    </ul>
  </div>
  <div class="badges" style="left:297px"><span class="badge"></span><span class="badge badge--mid"></span><span class="badge"></span></div>
  <div class="capsules"><span class="count">60</span><span class="word">Capsules</span><span class="per">470mg per serving</span></div>
  <div class="facts facts--dense" style="width:115px;left:504px;top:19px;height:182px">
    <h3>Supplement Facts</h3>
    <p class="serving" style="font-size:5px"><b>Serving Size:</b> 1 Capsule<br><b>Servings Per Container:</b> 60</p>
    <table>
      <tr><th></th><th>Amount Per Serving</th><th>%DV</th></tr>
      <tr><td>Vitamin C (as Ascorbic Acid)</td><td class="num">50 mg</td><td class="num">56%</td></tr>
      <tr><td>Vitamin E (as DL-Alpha Tocopheryl)</td><td class="num">7 mg</td><td class="num">47%</td></tr>
      <tr><td>Biotin</td><td class="num">300 mcg</td><td class="num">1,000%</td></tr>
      <tr><td>Magnesium (as Magnesium Oxide)</td><td class="num">125 mg</td><td class="num">30%</td></tr>
      <tr><td>Zinc (as Zinc Oxide)</td><td class="num">8 mg</td><td class="num">73%</td></tr>
      <tr><td>Manganese (as Manganese AAC)</td><td class="num">1 mg</td><td class="num">43%</td></tr>
      <tr><td>Chromium (as Chromium AAC)</td><td class="num">67 mcg</td><td class="num">191%</td></tr>
      <tr><td>Banaba Extract (1% Corosolic Acid)</td><td class="num">25 mg</td><td class="num">**</td></tr>
      <tr><td>Guggul (Commiphora mukul)</td><td class="num">50 mg</td><td class="num">**</td></tr>
      <tr><td>Bitter Melon Extract (fruit)</td><td class="num">20 mg</td><td class="num">**</td></tr>
      <tr><td>Licorice Extract (root)</td><td class="num">25 mg</td><td class="num">**</td></tr>
      <tr><td>Cinnamon Powder (bark)</td><td class="num">50 mg</td><td class="num">**</td></tr>
      <tr><td>Gymnema Extract (leaf)</td><td class="num">3 mg</td><td class="num">**</td></tr>
      <tr><td>Yarrow Powder (flower)</td><td class="num">25 mg</td><td class="num">**</td></tr>
      <tr><td>Cayenne Pepper Powder (fruit)</td><td class="num">10 mg</td><td class="num">**</td></tr>
      <tr><td>Juniper Extract (berry)</td><td class="num">13 mg</td><td class="num">**</td></tr>
      <tr><td>White Mulberry Extract (leaf)</td><td class="num">3 mg</td><td class="num">**</td></tr>
      <tr><td>Vanadium (as Vanadyl sulfate)</td><td class="num">2 mcg</td><td class="num">**</td></tr>
      <tr><td>Alpha Lipoic Acid</td><td class="num">30 mg</td><td class="num">**</td></tr>
      <tr><td>L-Taurine</td><td class="num">25 mg</td><td class="num">**</td></tr>
    </table>
    <p class="note" style="font-size:4.4px">** Daily Value (DV) not established.</p>
  </div>
  <p class="other" style="top:208px"><b>Other Ingredients:</b> Hypromellose (vegetable capsule), Rice Flour<span class="lot">V2R0<br>Lot # and Expiration Date Printed on bottom of bottle</span></p>
  <div class="strip"><div class="code-zone"></div><p class="distributor"><b>Distributed By:</b> Brookvale Wellness LLC<br>1420 Alder Ridge Rd. Laramie, WY 82070<br>www.brookvalewellness.example 555-014-2290</p></div>
</section>

<section class="label label--energy">
  <div class="usage">
    <p><b>SUGGESTED USE:</b> As a dietary supplement, take two (2) capsules once a day. For best results, take with food with an 8 fl oz. glass of water or as directed by your healthcare professional.</p>
    <p><b>CAUTION:</b> Do not exceed recommended dose. Pregnant or nursing mothers, children under the age of 18, and individuals with a known medical condition should consult a physician before using this or any dietary supplement.</p>
    <p class="keep">KEEP OUT OF REACH OF CHILDREN. DO NOT USE IF SAFETY SEAL IS DAMAGED OR MISSING. STORE IN A COOL, DRY PLACE.</p>
    <p class="fda-note">*These statements have not been evaluated by the Food and Drug Administration. This product is not intended to diagnose, treat, cure or prevent any disease.</p>
    <div class="brand"><span class="brand-mark"></span><span><span class="brand-name">BROOKVALE WELLNESS</span><span class="brand-url">www.brookvalewellness.example</span></span></div>
  </div>
  <div class="art" role="img" aria-label="Metal gears" style="left:410px;top:76px;width:66px;height:60px;background:radial-gradient(circle,#e6e6e6,#8a8a8a 70%,transparent 72%)"></div>
  <div class="front">
    <h1 class="title" style="font-size:36px;margin:6px 0 6px 0">VitalSpark<br>B-Complex<sup>TM</sup></h1>
    <span class="band band--red" style="width:208px;font-size:15px">With Vitamin B-12</span>
    <span class="band band--blue" style="width:208px">Dietary Supplement | 30-day supply</span>
    <ul class="benefits" style="gap:8px;margin-top:12px">
      <li><svg viewBox="0 0 10 10"><path d="M1 5l3 3 5-7" fill="none" stroke="var(--tick)" stroke-width="1.8"/></svg>Boosts energy levels*</li>
      <li><svg viewBox="0 0 10 10"><path d="M1 5l3 3 5-7" fill="none" stroke="var(--tick)" stroke-width="1.8"/></svg>Improves mental health*</li>
      <li><svg viewBox="0 0 10 10"><path d="M1 5l3 3 5-7" fill="none" stroke="var(--tick)" stroke-width="1.8"/></svg>Supports metabolism*</li>
    </ul>
  </div>
  <div class="badges" style="left:296px"><span class="badge"></span><span class="badge badge--mid"></span><span class="badge"></span></div>
  <div class="capsules" style="left:399px;top:192px"><span class="count">60</span><span class="word">Capsules</span><span class="per">982mg per serving</span></div>
  <div class="facts" style="left:507px;top:20px;width:142px;height:172px">
    <h3>Supplement Facts</h3>
    <p class="serving"><b>Serving Size:</b> 2 Capsules<br><b>Servings Per Container:</b> 30</p>
    <table style="font-size:4.9px">
      <tr><th></th><th>Amount Per Serving</th><th>%DV</th></tr>
      <tr><td>Vitamin C (as Ascorbic Acid)</td><td class="num">150mg</td><td class="num">167%</td></tr>
      <tr><td>Thiamin (as Thiamin Mononitrate)</td><td class="num">100mg</td><td class="num">8,333%</td></tr>
      <tr><td>Riboflavin (as Vitamin B2)</td><td class="num">100mg</td><td class="num">7,692%</td></tr>
      <tr><td>Niacin (as Niacinamide)</td><td class="num">20mg NE</td><td class="num">125%</td></tr>
      <tr><td>Vitamin B6 (as Pyridoxine HCl)</td><td class="num">30mg</td><td class="num">1,765%</td></tr>
      <tr><td>Folate<br>&nbsp;</td><td class="num">1190mcg DFE<br>(as 700mcg Folic Acid)</td><td class="num">298%<br>&nbsp;</td></tr>
      <tr><td>Vitamin B12 (as Cyanocobalamin)</td><td class="num">2000mcg</td><td class="num">83,333%</td></tr>
      <tr><td>Biotin</td><td class="num">1000mcg</td><td class="num">3,333%</td></tr>
      <tr><td>Pantothenic acid<br>(as D-Calcium Pantothenate)</td><td class="num">100mg<br>&nbsp;</td><td class="num">2,000%<br>&nbsp;</td></tr>
      <tr><td>Choline (as Choline Bitartrate)</td><td class="num">100mg</td><td class="num">18%</td></tr>
      <tr><td>Inositol</td><td class="num">150mg</td><td class="num">**</td></tr>
    </table>
    <p class="note">** Daily Value (DV) not established.</p>
  </div>
  <p class="other" style="top:198px"><b>Other Ingredients:</b> Hypromellose (vegetable capsule), Microcrystalline Cellulose, Vegetable Stearate.<span class="lot" style="margin-top:14px">V2R0<br>Lot # and Expiration Date Printed on bottom of bottle</span></p>
  <div class="strip"><div class="code-zone"></div><p class="distributor"><b>Distributed By:</b> Brookvale Wellness LLC<br>1420 Alder Ridge Rd. Laramie, WY 82070<br>www.brookvalewellness.example 555-014-2290</p></div>
</section>

<section class="label label--calm">
  <div class="usage">
    <p><b>Suggested Use:</b> As a dietary supplement, take two (2) veggie capsules once a day. For best results, take 20-30 min before a meal with an 8 fl oz. glass of water or as directed by your health care professional.</p>
    <p><b>Caution:</b> Do not exceed recommended dose. Pregnant or nursing mothers, children under the age of 18, and individuals with a known medical condition should consult a physician before using this or any dietary supplement.</p>
    <p class="keep">KEEP OUT THE REACH OF CHILDREN, DO NOT USE IF SAFETY SEAL IS DAMAGED OR MISSING. STORE IN A COOL, DRY PLACE.</p>
    <p class="fda-note">*These statements have not been evaluated by the Food and Drug Administration. This product is not intended to diagnose, treat, cure or prevent any disease.</p>
    <div class="brand"><span class="brand-mark"></span><span><span class="brand-name">BROOKVALE WELLNESS</span><span class="brand-url">www.brookvalewellness.example</span></span></div>
  </div>
  <div class="art" role="img" aria-label="White feather" style="left:410px;top:10px;width:62px;height:96px;background:radial-gradient(ellipse,#f4f4f8,#a9a3bd 65%,transparent 70%)"></div>
  <div class="front">
    <h1 class="title" style="font-size:40px;margin:6px 0 10px 0">CalmHaven<br>Max<sup>TM</sup></h1>
    <span class="band band--red" style="width:220px">Daily Stress Management Support*</span>
    <span class="band band--gold" style="width:220px;padding:5px 8px">Dietary Supplement | 30-day supply</span>
    <ul class="benefits" style="margin-left:8px">
      <li><svg viewBox="0 0 10 10"><path d="M1 5l3 3 5-7" fill="none" stroke="var(--tick)" stroke-width="1.8"/></svg>Promotes cognitive health*</li>
      <li><svg viewBox="0 0 10 10"><path d="M1 5l3 3 5-7" fill="none" stroke="var(--tick)" stroke-width="1.8"/></svg>May help calm stress*</li>
      <li><svg viewBox="0 0 10 10"><path d="M1 5l3 3 5-7" fill="none" stroke="var(--tick)" stroke-width="1.8"/></svg>Supports relaxed mood*</li>
    </ul>
  </div>
  <div class="badges" style="left:305px;bottom:10px"><span class="badge"></span><span class="badge badge--mid"></span><span class="badge"></span></div>
  <div class="capsules"><span class="count">60</span><span class="word">Capsules</span><span class="per">982mg per serving</span></div>
  <div class="facts facts--dense" style="width:143px;left:506px;top:20px;height:172px">
    <h3 style="font-size:16px">Supplement Facts</h3>
    <p class="serving" style="font-size:4.8px"><b>Serving Size:</b> 2 Veggie Capsules / <b>Servings Per Container:</b> 30</p>
    <table style="font-size:4.5px">
      <tr><th></th><th>Amount Per Serving</th><th>%DV</th></tr>
      <tr><td>Thiamin (as Thiamine Mononitrate)</td><td class="num">12 mg</td><td class="num">1,000%</td></tr>
      <tr><td>Riboflavin (Vitamin B2)</td><td class="num">12 mg</td><td class="num">923%</td></tr>
      <tr><td>Niacin (as Niacin)</td><td class="num">28 mg NE</td><td class="num">175%</td></tr>
      <tr><td>Vitamin B6 (as Pyridoxine HCl)</td><td class="num">8 mg</td><td class="num">471%</td></tr>
      <tr><td>Biotin</td><td class="num">300 mcg</td><td class="num">1,000%</td></tr>
      <tr><td>Pantothenic Acid (as D-Calcium Pantothenate)</td><td class="num">16 mg</td><td class="num">320%</td></tr>
      <tr><td>Calcium (as Calcium Carbonate)</td><td class="num">25 mg</td><td class="num">2%</td></tr>
      <tr><td>Magnesium (as Magnesium Oxide)</td><td class="num">25 mg</td><td class="num">6%</td></tr>
      <tr><td>Zinc (as Zinc Oxide)</td><td class="num">25 mg</td><td class="num">227%</td></tr>
      <tr><td style="border-top:1.5px solid var(--ink)"><b>Proprietary Blend</b></td><td class="num" style="border-top:1.5px solid var(--ink)">831 mg</td><td class="num" style="border-top:1.5px solid var(--ink)">**</td></tr>
      <tr><td colspan="3" class="blend">Rhodiola Extract (root), Lutein, Ashwagandha (root), Chamomile (flower), GABA, Lemon Balm (leaf), Chinese Skullcap (root), Hawthorn (fruit), Bacopa (whole herb), Magnolia (bark), Passion Flower (herb), Valerian (root), L-Theanine, Oat Straw, L-Phenylalanine, St John's Wort (aerial), Hops (flower), 5-HTP (seed)</td></tr>
    </table>
    <p class="note" style="font-size:4.4px">** Daily Value (DV) not established.</p>
  </div>
  <p class="other" style="top:198px"><b>Other Ingredients:</b> Rice Flour, Hypromellose (vegetable capsule), Potassium Gluconate, Magnesium Stearate (Vegetable), Silicon Dioxide.<span class="lot">V8R0<br>Lot # and Expiration Date Printed on bottom of bottle</span></p>
  <div class="strip"><div class="code-zone"></div><p class="distributor"><b>Distributed By:</b> Brookvale Wellness LLC<br>1420 Alder Ridge Rd. Laramie, WY 82070<br>www.brookvalewellness.example 555-014-2290</p></div>
</section>

</body>
</html>
```